Business Card Design for a Personal Trainer

I need a business card design for my job as a personal trainer. It should have a unique, modern and exclusive design. On the front there should be only my logo with my name and my job. 0162/3819204 Tobias Lendhart Wiesengrundweg 14 80417 Munich Germany The most important contact information is the web adress. it can be bigger than the rest, but its not necessary. The card should be 8,5cmx5,5cm big. Font: Roboto. Colors: black, white, gray, 56c1ff.

```html
<!DOCTYPE html>
<html lang="de">
<head>
<meta charset="utf-8">
<title>Tobias Lendhart – Personal Trainer Visitenkarte</title>
<link rel="stylesheet" href="https://fonts.googleapis.com/css2?family=Roboto:wght@300;400&display=swap">
<style>
  :root {
    --backdrop: #6f6f6f;
    --card-dark: #232323;
    --band: #3b3b3b;
    --white: #ffffff;
    --rule: #8a8a8a;
    --photo-light: #f2f2f2;
    --photo-mid: #9a9a9a;
    --photo-dark: #4a4a4a;
  }
  html, body {
    margin: 0;
    width: 1200px;
    height: 1200px;
    overflow: hidden;
    background: var(--backdrop);
    font-family: "Roboto", sans-serif;
  }
  .canvas { position: relative; width: 1200px; height: 1200px; }
  .card {
    position: absolute;
    top: 310px;
    width: 364px;
    height: 595px;
    overflow: hidden;
    box-shadow: 0 2px 6px rgba(0,0,0,0.35);
  }
  .card--contact { left: 234px; background: var(--white); }
  .card--brand { left: 630px; background: var(--card-dark); color: var(--white); }

  .portrait {
    position: absolute;
    inset: 0;
    background:
      radial-gradient(ellipse 150px 210px at 50% 62%, var(--photo-dark) 0%, var(--photo-mid) 70%, transparent 72%),
      linear-gradient(var(--white), var(--photo-light));
  }
  .contact-band {
    position: absolute;
    left: 0; right: 0; bottom: 0;
    height: 182px;
    background: var(--band);
    color: var(--white);
    text-align: center;
    font-size: 17px;
    font-weight: 400;
    line-height: 22px;
  }
  .contact-band p { margin: 0; }
  .contact-band .phone { margin-top: 40px; }
  .contact-band .divider {
    width: 150px; height: 1px; margin: 10px auto 9px;
    background: var(--rule);
  }

  .brand-name {
    position: absolute;
    top: 265px; left: 0; right: 0;
    text-align: center;
    font-size: 31px;
    font-weight: 300;
    letter-spacing: 0.5px;
    margin: 0;
  }
  .brand-role {
    position: absolute;
    top: 300px; left: 30px; right: 30px;
    display: flex; align-items: center; gap: 8px;
    font-size: 13px; font-weight: 400; letter-spacing: 3.2px;
    margin: 0;
  }
  .brand-role::before, .brand-role::after {
    content: ""; flex: 1; height: 1.5px; background: var(--white);
  }
  .website {
    position: absolute;
    top: 517px; left: 0; right: 0;
    text-align: center;
    font-size: 19px; font-weight: 400; letter-spacing: 0.5px;
    margin: 0;
  }
</style>
</head>
<body>
<main class="canvas">
  <section class="card card--contact">
    <div class="portrait" role="img" aria-label="Schwarz-Weiß-Porträt des Trainers mit verschränkten Armen"></div>
    <div class="contact-band">
      <p class="phone">0162/3819204</p>
      <p class="email">t.lendhart@postfach-mail.de</p>
      <div class="divider"></div>
      <p class="street">Wiesengrundweg 14</p>
      <p class="city">80417 München</p>
    </div>
  </section>

  <section class="card card--brand">
    <h1 class="brand-name">TOBIAS LENDHART</h1>
    <p class="brand-role">PERSONAL TRAINER</p>
    <p class="website">WWW.TOBIASLENDHART.DE</p>
  </section>
</main>
</body>
</html>
```